Video Production Company Website

A video production company website for "Copper Fern Productions"
Home page must have video player and way to select between 3 different videos.

Company does video Post production : Editing, Motion Graphics, Color correction, and Aerial videography
Attached company Logo

Design should be simple but Pro looking..

Earthy color palette with slight texture..

Industry/Entity Type

Film Production

Number of Pages Required

3 page

Font styles to use
Sans Serif
Other font styles liked:

Requirements
Nice to have
• Thumbnails on homepage to past project clips
Should not have
• full page video

```html
<!DOCTYPE html>
<html lang="en">
<head>
<meta charset="utf-8">
<title>Copper Fern Productions</title>
<link href="https://fonts.googleapis.com/css2?family=Oswald:wght@400;500;600&family=Open+Sans:wght@400;600;700&display=swap" rel="stylesheet">
<style>
:root{
  --mint:#5fcb97;
  --mint-dark:#3fae7c;
  --sand:#efe6d6;
  --paper:#f5f3ef;
  --card:#ecebe8;
  --ink:#2e2e2e;
  --muted:#8a8a8a;
  --night:#262626;
  --white:#ffffff;
  --photo-dark:#2d2f33;
  --photo-mid:#55585c;
}
*{box-sizing:border-box;margin:0;padding:0}
html,body{width:1200px;height:2616px;overflow:hidden}
body{position:relative;background:var(--paper);font-family:"Open Sans",Arial,sans-serif;color:var(--ink)}
.block{position:absolute;left:0;width:1200px}

/* header */
.site-header{top:0;height:60px;background:var(--sand);border-bottom:1px solid #dcd2c0}
.brand{position:absolute;left:88px;top:14px;display:flex;align-items:center;gap:8px;font-family:"Oswald",sans-serif;font-weight:600;font-size:26px;color:#4a4038;letter-spacing:.5px}
.brand-dot{width:12px;height:12px;border-radius:50%;background:var(--mint)}
.main-nav{position:absolute;right:88px;top:0;height:60px;display:flex;align-items:center;gap:30px;font-size:11px;font-weight:600;letter-spacing:.8px;color:#5b544c}
.main-nav .current{color:var(--ink)}

/* hero */
.hero{top:60px;height:740px}
.hero-photo{position:absolute;inset:0;background:linear-gradient(100deg,#3a3d42 0%,#1f2124 45%,#4b4e52 75%,#2a2c2f 100%)}
.hero-title{position:absolute;top:290px;width:100%;text-align:center;font-family:"Oswald",sans-serif;font-weight:500;font-size:60px;letter-spacing:3px;color:var(--white)}
.hero-cta{position:absolute;top:392px;left:496px;width:208px;height:40px;background:var(--mint);color:var(--white);font-size:11px;font-weight:700;letter-spacing:1px;display:flex;align-items:center;justify-content:center;gap:10px}
.slide-arrow{position:absolute;top:400px;width:34px;height:34px;border-radius:50%;background:var(--white);display:flex;align-items:center;justify-content:center}
.slide-arrow.prev{left:24px}.slide-arrow.next{right:24px}
.hero-edge{position:absolute;left:0;bottom:0}

/* welcome */
.section-title{position:absolute;width:100%;text-align:center;font-family:"Oswald",sans-serif;font-weight:500;font-size:24px;letter-spacing:1.5px;color:var(--ink)}
.section-title::after{content:"";display:block;width:60px;height:2px;background:var(--mint);margin:10px auto 0}
.welcome-title{top:864px}
.welcome-text{top:920px;left:200px;width:800px;text-align:center;font-size:13px;line-height:22px;color:var(--muted)}

/* services */
.service{position:absolute;top:1032px;width:280px;height:216px}
.service svg.service-shape{position:absolute;inset:0}
.service-icon{position:absolute;left:110px;top:20px;width:60px;height:60px;background:#dcdad5;display:flex;align-items:center;justify-content:center}
.service-name{position:absolute;top:96px;width:100%;text-align:center;font-size:13px;font-weight:700;letter-spacing:1px}
.service-text{position:absolute;top:120px;left:40px;width:200px;text-align:center;font-size:11px;line-height:17px;color:var(--muted)}

/* video band */
.reel-band{top:1290px;height:360px}
.reel-band svg{position:absolute;inset:0}
.reel-title{position:absolute;top:140px;width:100%;text-align:center;font-family:"Oswald",sans-serif;font-weight:500;font-size:48px;letter-spacing:2px;color:var(--white)}
.reel-sub{position:absolute;top:206px;width:100%;text-align:center;font-family:"Oswald",sans-serif;font-size:30px;letter-spacing:2px;color:var(--white)}

/* projects */
.projects-title{top:1714px}
.project-thumb{position:absolute;width:320px;height:200px;overflow:hidden}
.project-thumb .clip{position:absolute;inset:0}
.player-bar{position:absolute;left:0;bottom:0;width:100%;height:22px;background:rgba(0,0,0,.7);display:flex;align-items:center;gap:8px;padding:0 8px}
.player-track{flex:1;height:4px;background:#777}
.player-track span{display:block;width:30%;height:100%;background:var(--mint)}

/* connect */
.connect{top:2288px;height:252px;background:var(--mint)}
.connect-title{position:absolute;top:30px;width:100%;text-align:center;font-family:"Oswald",sans-serif;font-weight:500;font-size:24px;letter-spacing:1.5px;color:var(--white)}
.social-row{position:absolute;top:82px;left:0;width:100%;display:flex;justify-content:center;gap:18px}
.social-row span{width:40px;height:40px;border-radius:50%;background:var(--white)}
.newsletter{position:absolute;top:168px;left:400px;display:flex;gap:10px}
.newsletter .field{width:290px;height:40px;background:var(--white);font-size:11px;color:#999;padding-left:14px;display:flex;align-items:center}
.newsletter .button{width:100px;height:40px;background:var(--sand);font-size:11px;font-weight:700;letter-spacing:1px;display:flex;align-items:center;justify-content:center;color:var(--ink)}

/* footer */
.site-footer{top:2540px;height:76px;background:var(--night);color:#aaa;font-size:11px;display:flex;align-items:center;justify-content:center}
</style>
</head>
<body>

<header class="block site-header">
  <div class="brand"><span>copperfern</span><span class="brand-dot"></span></div>
  <nav class="main-nav">
    <span class="current">HOME</span><span>ABOUT US</span><span>OUR PROJECTS</span><span>STUDIO</span><span>BLOG</span><span>CONTACT US</span>
    <svg width="14" height="14" viewBox="0 0 14 14"><circle cx="6" cy="6" r="4.5" fill="none" stroke="#5b544c" stroke-width="1.6"/><line x1="9.5" y1="9.5" x2="13" y2="13" stroke="#5b544c" stroke-width="1.8"/></svg>
  </nav>
</header>

<section class="block hero">
  <div class="hero-photo" role="img" aria-label="Camera operator working behind studio video equipment"></div>
  <h1 class="hero-title">COPPER FERN PRODUCTIONS</h1>
  <div class="hero-cta">FIND OUR DEMO REEL
    <svg width="12" height="10" viewBox="0 0 12 10"><rect x="0" y="1" width="8" height="8" fill="#fff"/><polygon points="8,5 12,2 12,8" fill="#fff"/></svg>
  </div>
  <div class="slide-arrow prev"><svg width="12" height="12" viewBox="0 0 12 12"><polyline points="8,1 3,6 8,11" fill="none" stroke="#333" stroke-width="2"/></svg></div>
  <div class="slide-arrow next"><svg width="12" height="12" viewBox="0 0 12 12"><polyline points="4,1 9,6 4,11" fill="none" stroke="#333" stroke-width="2"/></svg></div>
  <svg class="hero-edge" width="1200" height="140" viewBox="0 0 1200 140">
    <polygon points="0,40 600,110 1200,20 1200,140 0,140" fill="var(--mint)"/>
    <polygon points="0,90 600,130 1200,70 1200,140 0,140" fill="var(--paper)"/>
  </svg>
</section>

<h2 class="section-title welcome-title">WELCOME TO COPPER FERN PRODUCTIONS</h2>
<p class="block welcome-text" style="left:200px;width:800px">We shape raw footage into stories that move people. From the first cut to the final grade, our small team works closely with directors, brands and creators to deliver polished video on time. Every project gets careful editing, clean motion design and color that feels true to the story you want to tell on screen.</p>

<div class="service" style="left:100px">
  <svg class="service-shape" width="280" height="216" viewBox="0 0 280 216"><polygon points="0,0 280,0 280,186 140,216 0,186" fill="var(--mint)"/><polygon points="0,0 280,0 280,180 140,208 0,180" fill="var(--card)"/></svg>
  <div class="service-icon"><svg width="26" height="26" viewBox="0 0 26 26"><polygon points="4,22 6,15 18,3 23,8 11,20" fill="#fff"/></svg></div>
  <div class="service-name">EDITING</div>
  <p class="service-text">We trim, pace and assemble your footage into a clear story.</p>
</div>
<div class="service" style="left:460px">
  <svg class="service-shape" width="280" height="216" viewBox="0 0 280 216"><polygon points="0,0 280,0 280,186 140,216 0,186" fill="var(--mint)"/><polygon points="0,0 280,0 280,180 140,208 0,180" fill="var(--card)"/></svg>
  <div class="service-icon"><svg width="30" height="22" viewBox="0 0 30 22"><rect x="0" y="3" width="20" height="16" rx="2" fill="#fff"/><polygon points="21,11 30,4 30,18" fill="#fff"/></svg></div>
  <div class="service-name">MOTION GRAPHICS</div>
  <p class="service-text">Titles, lower thirds and animated graphics that add energy.</p>
</div>
<div class="service" style="left:820px">
  <svg class="service-shape" width="280" height="216" viewBox="0 0 280 216"><polygon points="0,0 280,0 280,186 140,216 0,186" fill="var(--mint)"/><polygon points="0,0 280,0 280,180 140,208 0,180" fill="var(--card)"/></svg>
  <div class="service-icon"><svg width="30" height="24" viewBox="0 0 30 24"><rect x="1" y="1" width="28" height="22" fill="none" stroke="#fff" stroke-width="2"/><polygon points="4,20 12,10 18,16 21,13 26,20" fill="#fff"/><circle cx="22" cy="7" r="2.5" fill="#fff"/></svg></div>
  <div class="service-name">COLOR CORRECTION</div>
  <p class="service-text">Balanced, graded color for a consistent cinematic look.</p>
</div>

<section class="block reel-band">
  <svg width="1200" height="360" viewBox="0 0 1200 360">
    <polygon points="0,70 520,20 560,80 0,150" fill="var(--mint)"/>
    <polygon points="640,280 1200,210 1200,290 680,340" fill="var(--mint)"/>
    <defs><linearGradient id="reelTone" x1="0" x2="1"><stop offset="0" stop-color="#23262b"/><stop offset=".5" stop-color="#4a5a6a"/><stop offset="1" stop-color="#1e2125"/></linearGradient></defs>
    <polygon points="0,110 460,40 740,0 1200,120 1200,250 740,330 460,360 0,260" fill="url(#reelTone)" role="img" aria-label="Editing suite footage playing on a monitor"/>
  </svg>
  <h2 class="reel-title">COPPER FERN PRODUCTIONS VIDEOS</h2>
  <p class="reel-sub">OUR VIDEO PROFESSIONALS ARE HERE FOR YOU</p>
</section>

<h2 class="section-title projects-title">PAST PROJECTS</h2>

<div class="project-thumb" style="left:100px;top:1788px"><div class="clip" role="img" aria-label="Documentary title card over a blue sky" style="background:linear-gradient(135deg,#2f5d9a,#1c2a44)"></div><div class="player-bar"><svg width="8" height="10"><polygon points="0,0 8,5 0,10" fill="#fff"/></svg><div class="player-track"><span></span></div></div></div>
<div class="project-thumb" style="left:440px;top:1788px"><div class="clip" role="img" aria-label="Street scene at dusk" style="background:linear-gradient(135deg,#5a3a38,#2a1c1e)"></div><div class="player-bar"><svg width="8" height="10"><polygon points="0,0 8,5 0,10" fill="#fff"/></svg><div class="player-track"><span></span></div></div></div>
<div class="project-thumb" style="left:780px;top:1788px"><div class="clip" role="img" aria-label="Speaker on a stage with a blue screen" style="background:linear-gradient(135deg,#25457a,#3a2a3a)"></div><div class="player-bar"><svg width="8" height="10"><polygon points="0,0 8,5 0,10" fill="#fff"/></svg><div class="player-track"><span></span></div></div></div>
<div class="project-thumb" style="left:100px;top:2028px"><div class="clip" role="img" aria-label="Two people in a warm interior interview" style="background:linear-gradient(135deg,#7a5a48,#3a2c28)"></div><div class="player-bar"><svg width="8" height="10"><polygon points="0,0 8,5 0,10" fill="#fff"/></svg><div class="player-track"><span></span></div></div></div>
<div class="project-thumb" style="left:440px;top:2028px"><div class="clip" role="img" aria-label="Outdoor interview among green trees" style="background:linear-gradient(135deg,#5f7a48,#2e3a26)"></div><div class="player-bar"><svg width="8" height="10"><polygon points="0,0 8,5 0,10" fill="#fff"/></svg><div class="player-track"><span></span></div></div></div>
<div class="project-thumb" style="left:780px;top:2028px"><div class="clip" role="img" aria-label="Group photo on a bright event stage" style="background:linear-gradient(135deg,#c9a48a,#7a4a3a)"></div><div class="player-bar"><svg width="8" height="10"><polygon points="0,0 8,5 0,10" fill="#fff"/></svg><div class="player-track"><span></span></div></div></div>

<section class="block connect">
  <h2 class="connect-title">CONNECT WITH US</h2>
  <div class="social-row"><span></span><span></span><span></span><span></span><span></span></div>
  <div class="newsletter"><div class="field">EMAIL ADDRESS</div><div class="button">SUBSCRIBE</div></div>
</section>

<footer class="block site-footer">© Copyright 2015 Copper Fern Productions, All rights reserved.</footer>

</body>
</html>
```